Redesign Website - Current one too plain

The description is in the uploaded file. Please let me know if you need any more information. I'd prefer it if someone could implement the design to a WordPress site but the best design will win, regardless.
I would like the forms to look nice as well
UPDATE:
I don't think we can use the images that I provided, I think they make the site look a bit 'cheap' and I really don't know how to replace them. One thought I have had is to make the "Simple, Unique, Effective" a second feature on the right side of the page with the search on the left
Target Market(s)
Small companies, private sellers of cars and people who rent their caravan/holiday home out
Industry/Entity Type
Advertising
Number of Pages Required
3 page
Colors
Designer to choose colors to be used in the design.
Look and feel
Each slider illustrates characteristics of the customer's brand and the style your logo design should communicate.

```html
<!DOCTYPE html>
<html lang="en">
<head>
<meta charset="utf-8">
<title>PLAKO – Discover And Connect</title>
<link href="https://fonts.googleapis.com/css2?family=Inter:wght@400;500;600;700&display=swap" rel="stylesheet">
<style>
  :root{
    --bg:#232323;
    --lime:#eafc52;
    --white:#ffffff;
    --ink:#1c1c1c;
    --card:#232323;
    --photo-a:#4a4a48;
    --photo-b:#9a9894;
  }
  *{box-sizing:border-box;margin:0;padding:0}
  html,body{width:1200px;height:3824px;overflow:hidden}
  body{background:var(--bg);color:var(--white);font-family:"Inter",Arial,sans-serif;position:relative}
  .abs{position:absolute}

  /* header */
  .brand{left:85px;top:34px;display:flex;align-items:center;gap:10px;color:var(--lime);font-size:24px;font-weight:500;letter-spacing:1px}
  .brand-dot{width:26px;height:26px;border-radius:50%;background:var(--lime)}
  .nav{top:44px;left:0;width:1200px;height:20px}
  .nav a{position:absolute;color:var(--white);text-decoration:none;font-size:13px;font-weight:500}
  .btn{display:flex;align-items:center;justify-content:center;background:var(--lime);color:var(--ink);border-radius:20px;font-size:17px;font-weight:500;text-decoration:none}
  .login{left:977px;top:35px;width:137px;height:36px}

  /* hero */
  .hero-title{top:138px;width:1200px;text-align:center;font-size:60px;font-weight:700;letter-spacing:.5px}
  .hero-sub{top:222px;width:1200px;text-align:center;font-size:17px;font-weight:500}
  .code-char{top:295px;width:80px;text-align:center;color:var(--lime);font-size:96px;font-weight:600;line-height:110px}
  .chev{width:16px;height:16px}
  .chip{top:439px;height:32px;border:1.5px solid var(--lime);border-radius:16px;color:var(--lime);font-size:17px;display:flex;align-items:center;justify-content:center}
  .search{left:480px;top:500px;width:239px;height:35px}
  .photo{background:linear-gradient(180deg,var(--photo-a),var(--photo-b));border-radius:18px}
  .hero-photo{left:160px;top:612px;width:860px;height:240px}

  /* about */
  .about{left:57px;top:822px;width:1086px;height:480px;background:var(--white);border-radius:30px}
  .about h2{position:absolute;top:62px;width:100%;text-align:center;color:var(--ink);font-size:26px;font-weight:600}
  .feature{top:153px;width:267px;height:266px;background:var(--card);border-radius:28px;text-align:center}
  .feature svg{position:absolute;left:93px;top:50px}
  .feature h3{position:absolute;top:154px;width:100%;color:var(--lime);font-size:22px;font-weight:600}
  .feature p{position:absolute;top:188px;left:30px;width:207px;font-size:13px;line-height:15px}

  /* how it works */
  .how-title{left:98px;top:1357px;color:var(--lime);font-size:26px;font-weight:600}
  .steps{left:98px;top:1444px;width:470px;font-size:16.5px;line-height:28.5px;font-weight:500}
  .steps p{margin-bottom:28.5px}
  .step-icon{width:76px;height:76px;background:var(--lime);border-radius:14px;display:flex;align-items:center;justify-content:center;color:var(--ink)}
  .step-label{width:180px;text-align:center;font-size:16.5px;line-height:28.5px;font-weight:500}
  .a1{font-size:54px;font-weight:600}
  .vehicles{left:75px;top:2035px;width:1040px;height:340px}

  /* why */
  .why{left:57px;top:2440px;width:1086px;height:397px;background:var(--lime);border-radius:30px;color:var(--ink)}
  .why h2{position:absolute;top:50px;width:100%;text-align:center;font-size:26px;font-weight:600}
  .why-body{position:absolute;left:66px;top:144px;width:960px;font-size:16.5px;line-height:28.5px;font-weight:500}
  .why-body ul{margin-left:26px}

  /* cta */
  .cta-title{top:2900px;width:1200px;text-align:center;font-size:26px;font-weight:600}
  .cta-text{left:135px;top:2992px;width:930px;font-size:16.5px;line-height:28.5px;font-weight:500}
  .signup{left:481px;top:3125px;width:238px;height:35px}
</style>
</head>
<body>

<header>
  <div class="abs brand"><span class="brand-dot"></span>PLAKO</div>
  <nav class="abs nav">
    <a style="left:410px" href="#">Home</a>
    <a style="left:487px" href="#">Advertise</a>
    <a style="left:592px" href="#">Contact</a>
    <a style="left:698px" href="#">Register</a>
  </nav>
  <a class="abs btn login" href="#">Login</a>
</header>

<section class="hero">
  <h1 class="abs hero-title">Discover And Connect</h1>
  <p class="abs hero-sub">Display Your Unique Code on Your Vehicle to Attract Customers</p>

  <svg class="abs chev" style="left:538px;top:292px" viewBox="0 0 16 16"><circle cx="8" cy="8" r="7.5" fill="var(--lime)"/><path d="M4.5 10 8 6.5 11.5 10" stroke="#232323" stroke-width="2" fill="none"/></svg>
  <svg class="abs chev" style="left:623px;top:292px" viewBox="0 0 16 16"><circle cx="8" cy="8" r="7.5" fill="var(--lime)"/><path d="M4.5 10 8 6.5 11.5 10" stroke="#232323" stroke-width="2" fill="none"/></svg>
  <div class="abs code-char" style="left:506px">S</div>
  <div class="abs code-char" style="left:591px">6</div>
  <svg class="abs chev" style="left:538px;top:394px" viewBox="0 0 16 16"><circle cx="8" cy="8" r="7.5" fill="var(--lime)"/><path d="M4.5 6 8 9.5 11.5 6" stroke="#232323" stroke-width="2" fill="none"/></svg>
  <svg class="abs chev" style="left:623px;top:394px" viewBox="0 0 16 16"><circle cx="8" cy="8" r="7.5" fill="var(--lime)"/><path d="M4.5 6 8 9.5 11.5 6" stroke="#232323" stroke-width="2" fill="none"/></svg>

  <div class="abs chip" style="left:438px;width:56px">Car</div>
  <div class="abs chip" style="left:529px;width:93px">Caravan</div>
  <div class="abs chip" style="left:657px;width:103px">Company</div>
  <a class="abs btn search" href="#">Search</a>

  <div class="abs photo hero-photo" role="img" aria-label="Photo of a static holiday caravan"></div>
</section>

<section class="abs about">
  <h2>About us</h2>
  <div class="abs feature" style="left:76px">
    <svg width="80" height="88" viewBox="0 0 80 88" fill="none" stroke="var(--lime)" stroke-width="3" stroke-linecap="round" stroke-linejoin="round">
      <path d="M30 80V50l-8-10c-3-4 2-8 6-5l6 6V20c0-4 6-4 6 0v18V14c0-4 6-4 6 0v24V18c0-4 6-4 6 0v22V26c0-4 6-4 6 0v30c0 12-6 24-18 24z"/>
      <path d="M40 2v6M28 6l3 5M52 6l-3 5"/>
    </svg>
    <h3>Simple</h3>
    <p>Create your advert and display your code</p>
  </div>
  <div class="abs feature" style="left:410px">
    <svg width="80" height="80" viewBox="0 0 80 80" fill="none" stroke="var(--lime)" stroke-width="3" stroke-linecap="round">
      <path d="M10 40a24 24 0 0 1 44-14M16 46a18 18 0 0 1 30-18M22 50a12 12 0 0 1 18-12M28 54a6 6 0 0 1 6-8"/>
      <circle cx="50" cy="52" r="13"/><path d="M60 62l12 12"/>
    </svg>
    <h3 style="top:150px">Unique</h3>
    <p style="top:184px">Customers find you by an easy-to-remember code</p>
  </div>
  <div class="abs feature" style="left:743px">
    <svg width="80" height="80" viewBox="0 0 80 80" fill="none" stroke="var(--lime)" stroke-width="3" stroke-linecap="round">
      <circle cx="40" cy="40" r="34"/><circle cx="40" cy="40" r="20"/><circle cx="40" cy="40" r="13"/>
      <path d="M40 33v7l5 4"/><path d="M66 14l4 8-8 1"/>
    </svg>
    <h3 style="top:150px">Effective</h3>
    <p style="top:184px">Customers are directed to you and not a list of your competitors</p>
  </div>
</section>

<section class="how">
  <h2 class="abs how-title">How it works</h2>
  <div class="abs steps">
    <p>Step 1:</p>
    <p>Generate your unique code and create an eye-catching advert that showcases your business. Highlight your products, services, and contact details to ensure customers can easily reach you.</p>
    <p style="margin-bottom:0">Step 2:</p>
    <p>Affix your code prominently on your vehicles. Whether it's a car, van, or caravan, your code will act as a beacon, guiding interested customers right to your doorstep.</p>
    <p>Step 3:</p>
    <p>Sit back and watch as customers effortlessly find and connect with your business using your memorable code. Increase your visibility and enhance your customer base with our innovative concept.</p>
  </div>

  <div class="abs step-icon" style="left:647px;top:1459px">
    <svg width="48" height="48" viewBox="0 0 48 48" fill="none" stroke="#1c1c1c" stroke-width="3"><rect x="4" y="4" width="30" height="26"/><path d="M4 12h30M10 20h18"/><rect x="22" y="30" width="20" height="14"/><circle cx="32" cy="37" r="3"/></svg>
  </div>
  <div class="abs step-label" style="left:595px;top:1541px">Step 1:<br>Create Your<br>Advert Content</div>
  <svg class="abs" style="left:758px;top:1490px" width="100" height="92" viewBox="0 0 100 92" fill="none" stroke="#fff" stroke-width="5" stroke-linecap="round"><path d="M3 10c40-6 70 14 80 70"/><path d="M68 66l15 16 12-20"/></svg>

  <div class="abs step-icon a1" style="left:823px;top:1617px">A1</div>
  <div class="abs step-label" style="left:771px;top:1706px">Step 2:<br>Display Your<br>Code Content</div>
  <svg class="abs" style="left:858px;top:1818px" width="112" height="76" viewBox="0 0 112 76" fill="none" stroke="#fff" stroke-width="5" stroke-linecap="round"><path d="M4 4c10 30 50 52 100 44"/><path d="M86 30l18 18-18 16"/></svg>

  <div class="abs step-icon" style="left:1000px;top:1808px">
    <svg width="50" height="46" viewBox="0 0 50 46" fill="#1c1c1c"><rect x="2" y="12" width="28" height="18" rx="3"/><circle cx="9" cy="21" r="2" fill="#eafc52"/><circle cx="16" cy="21" r="2" fill="#eafc52"/><circle cx="23" cy="21" r="2" fill="#eafc52"/><path d="M28 2h20v12H36l-4 4v-4h-4z" fill="none" stroke="#1c1c1c" stroke-width="2.5"/><rect x="2" y="34" width="26" height="8"/><path d="M32 44V32l6-8 2 8h8v12z"/></svg>
  </div>
  <div class="abs step-label" style="left:948px;top:1894px">Step 3:<br>Customers Find<br>Your Content</div>

  <div class="abs photo vehicles" role="img" aria-label="Photo of a silver SUV, a holiday caravan and a sign-written silver van"></div>
</section>

<section class="abs why">
  <h2>Why Choose Us</h2>
  <div class="why-body">
    <p>Our platform offers a user-friendly experience that empowers businesses of all sizes to increase their presence. With our easy-to-use system and eye-catching codes, you can enjoy these benefits:</p>
    <ul>
      <li>Stand out from competitors with a unique identifier</li>
      <li>Attract more customers with straightforward access to your business</li>
      <li>Increase your brand recognition and credibility</li>
      <li>Track the effectiveness of your adverts with real-time data</li>
    </ul>
  </div>
</section>

<section class="cta">
  <h2 class="abs cta-title">Ready to Elevate Your Business?</h2>
  <p class="abs cta-text">Don't miss out on this opportunity to simplify and optimize your customer connections. Sign up now and start displaying your code to grow your business and build stronger customer relationships.</p>
  <a class="abs btn signup" href="#">Sign up now</a>
</section>

</body>
</html>
```